Inspirational Quotes Poster Set

Brookloft is a stylish coworking space, which has a design-oriented vintage look from the 60's with an industrial touch (www.brookloft-example.com) Brookloft Quote Poster Set of 16 posters. The poster should be typo oriented and rather simple. Reflecting a bit the clean billboard design from the sixties. Minimal / simple graphical elements

Target Market(s)

Startups and Entrepreneurs

Industry/Entity Type

Startup

Font styles to use
Sans Serif

Colors

Designer to choose colors to be used in the design.

Requirements
Must have
• Posters need to be on and very stylish

```html
<!DOCTYPE html>
<html lang="en">
<head>
<meta charset="utf-8">
<title>Brookloft Quote Poster</title>
<link href="https://fonts.googleapis.com/css2?family=Archivo:wght@700;800&display=swap" rel="stylesheet">
<style>
  :root {
    --ink: #000000;
    --orange: #e65f1c;
    --orange-deep: #b8480f;
    --paper: #ffffff;
  }
  html, body {
    margin: 0;
    padding: 0;
    overflow: hidden;
    background: var(--ink);
  }
  .poster {
    position: relative;
    width: 801px;
    height: 1200px;
    overflow: hidden;
    background: var(--orange);
    font-family: "Archivo", "Helvetica Neue", Arial, sans-serif;
  }
  .poster__scene {
    position: absolute;
    left: 0;
    top: 0;
    width: 801px;
    height: 985px;
    background:
      radial-gradient(ellipse 300px 320px at 400px 350px, var(--orange) 0%, var(--orange) 70%, var(--orange-deep) 85%, var(--ink) 100%),
      var(--ink);
  }
  .poster__ground {
    position: absolute;
    left: 0;
    top: 985px;
    width: 801px;
    height: 215px;
    background: var(--orange);
  }
  .quote {
    position: absolute;
    inset: 0;
    width: 801px;
    height: 1200px;
    display: block;
  }
  .quote__line {
    fill: var(--paper);
    font-family: "Archivo", "Helvetica Neue", Arial, sans-serif;
    font-weight: 800;
    font-size: 98px;
    letter-spacing: -3.6px;
  }
  .attribution {
    position: absolute;
    left: 71px;
    top: 1024px;
    margin: 0;
    color: var(--paper);
    font-weight: 800;
    font-size: 22px;
    line-height: 28px;
    letter-spacing: -0.6px;
  }
  .brand {
    position: absolute;
    left: 70px;
    top: 1094px;
    margin: 0;
    color: var(--paper);
    font-weight: 800;
    font-size: 48px;
    line-height: 1;
    letter-spacing: -1.8px;
  }
</style>
</head>
<body>
<main class="poster">
  <div class="poster__scene" role="img" aria-label="Abstract illustration of an orange sun above a winding white road across orange hills on a black sky"></div>
  <div class="poster__ground"></div>
  <svg class="quote" viewBox="0 0 801 1200" aria-label="it’s hard to beat a person who never gives up" role="img">
    <g text-anchor="middle">
      <text class="quote__line" x="401" y="201">it’s hard</text>
      <text class="quote__line" x="400" y="290">to beat</text>
      <text class="quote__line" x="400" y="380">a person</text>
      <text class="quote__line" x="390" y="469">who never</text>
      <text class="quote__line" x="400" y="559">gives up</text>
    </g>
  </svg>
  <p class="attribution">Ray Hollister,<br>Baseball Legend</p>
  <p class="brand">brookloft</p>
</main>
</body>
</html>
```